Dynamic Business Card for Sports Supplements Company

Hi! I'm looking for an awesome business card to match my existing sports supplement company. I have uploaded my current company logo and screenshot of the front page of my website.

I would like to have something dynamic and interesting and utilize the colors in the website - the reds and purples

The business card should be double sided and focus on a unique eye-catching design on the back and include all the relevant company info.

Most importantly, it should say somewhere: "Sign up on our website for a coupon code."

Target Market(s)

Mostly for women gym goers but it shouldn't be too feminine. It should be in keeping with the website design. It should flow and clearly be connected to it

Industry/Entity Type

Business

Contact Information for Business Card

Lorraine K. Vestal
CEO
LVestal@Quorvanexco.com
www.quorvanexco.com
555.417.3820
P.O. Box 47315
Kestrelton, Arborland 00000

Sign up on our website for a coupon code

Font styles to use
Serif
Sans Serif
Other font styles liked:
• Novecento font family and "Quorvanex" is in AR Destine font

Requirements
Must have
• One side should be a bold Quorvanex logo design. Even just the symbol itself may be o.k. (see attached file)

```html
<!DOCTYPE html>
<html lang="en">
<head>
<meta charset="utf-8">
<title>Quorvanex Business Card</title>
<link rel="stylesheet" href="https://fonts.googleapis.com/css2?family=Montserrat:wght@600;700;800&family=Roboto:wght@400;500&display=swap">
<style>
  :root {
    --page: #e4e4e6;
    --card-dark: #141414;
    --card-light: #ffffff;
    --brand-red: #e52a2a;
    --ink-grey: #555555;
    --ink-soft: #6a6a6a;
    --white: #ffffff;
  }
  * { box-sizing: border-box; margin: 0; padding: 0; }
  html, body {
    width: 1200px; height: 1000px; overflow: hidden;
    background: var(--page);
  }
  .canvas { position: relative; width: 1200px; height: 1000px; }
  .card {
    position: absolute; left: 250px; width: 700px; height: 400px;
    border-radius: 28px;
    box-shadow: 0 10px 30px rgba(0,0,0,0.18);
    overflow: hidden;
  }
  .brand-mark {
    display: block; margin: 0 auto 14px;
    width: 64px; height: 64px;
  }
  .brand-name {
    font-family: "Montserrat", sans-serif; font-weight: 800;
    letter-spacing: 1px; line-height: 1;
  }
  .brand-tagline {
    font-family: "Montserrat", sans-serif; font-weight: 600;
    letter-spacing: 2px; margin-top: 8px;
  }

  /* Back side */
  .card-back { top: 70px; background: var(--card-dark); }
  .card-back .brand-lockup {
    position: absolute; left: 0; right: 0; top: 80px; text-align: center;
  }
  .card-back .brand-mark { background: var(--white); }
  .card-back .brand-name { color: var(--white); font-size: 50px; }
  .card-back .brand-tagline { color: var(--white); font-size: 16px; }
  .card-back .coupon-note {
    position: absolute; left: 0; right: 0; bottom: 48px; text-align: center;
    font-family: "Roboto", sans-serif; font-weight: 500; font-size: 17px;
    letter-spacing: 4px; color: var(--brand-red);
  }

  /* Front side */
  .card-front { top: 530px; background: var(--card-light); }
  .holder {
    position: absolute; left: 52px; top: 62px;
    font-family: "Montserrat", sans-serif;
  }
  .holder-name { font-size: 25px; font-weight: 700; color: var(--ink-grey); letter-spacing: 0.5px; }
  .holder-name .surname { color: var(--brand-red); }
  .holder-role { font-size: 13px; font-weight: 700; color: var(--ink-grey); margin-top: 6px; }
  .contact {
    position: absolute; left: 52px; bottom: 44px;
    font-family: "Roboto", sans-serif; font-size: 15px; line-height: 1.45; color: var(--ink-soft);
  }
  .contact .address { margin-bottom: 10px; }
  .contact .label, .contact .accent { color: var(--brand-red); }
  .card-front .brand-lockup {
    position: absolute; right: 48px; top: 70px; text-align: center;
  }
  .card-front .brand-mark { background: var(--brand-red); width: 80px; height: 80px; }
  .card-front .brand-name { color: var(--brand-red); font-size: 40px; }
  .card-front .brand-tagline { color: var(--brand-red); font-size: 13px; }
</style>
</head>
<body>
<main class="canvas">
  <section class="card card-back" aria-label="Card back">
    <div class="brand-lockup">
      <span class="brand-mark" aria-hidden="true"></span>
      <div class="brand-name">QUORVANEX</div>
      <div class="brand-tagline">your performance partner</div>
    </div>
    <p class="coupon-note">Sign up on our website for a coupon code</p>
  </section>

  <section class="card card-front" aria-label="Card front">
    <div class="holder">
      <div class="holder-name">LORRAINE <span class="surname">K. VESTAL</span></div>
      <div class="holder-role">CEO</div>
    </div>
    <div class="contact">
      <div class="address">P.O. Box 47315<br>Kestrelton, Arborland 00000</div>
      <div><span class="label">P:</span> 555.417.3820</div>
      <div><span class="label">E:</span> LVestal@Quorvanexco.com</div>
      <div><span class="label">W:</span> www.<span class="accent">quorvanexco</span>.com</div>
    </div>
    <div class="brand-lockup">
      <span class="brand-mark" aria-hidden="true"></span>
      <div class="brand-name">QUORVANEX</div>
      <div class="brand-tagline">your performance partner</div>
    </div>
  </section>
</main>
</body>
</html>
```